WeatheredOnward.net wordpress design

Concept: Website where personal stories, personal videos can be posted as a challenge while awaiting the wisdom of experience from others who have survived this same event or challenge in their lifetime.
Support aspects will be in 4 quadrants of Challenges:
1. Financial 2. Medical & Physical
3. Legal Matters 4. Psychological & Spiritual - ability to chat online with a spiritual/psychological counselor or life coach
Updates
Project Deadline Extended
Reason: Bit more time to complete designs.
Wanted to thank all of you for your designs! Greatly appreciated. Very creative ideas that captured the essence of this website. Will be back with a selection very shortly.
Target Market(s)
Anyone looking for a solution based upon experiential wisdom
Industry/Entity Type
Financial
Requirements
Must have
- Interactive website: Where you can post a challenge or issue via a written question or a video and ask for a solution.
Ability to access any of the 4 Quadrants (as listed above) to ask for an expert, via experience, advice and wisdom from those who have similar challenges.

```html
<!DOCTYPE html>
<html lang="en">
<head>
<meta charset="utf-8">
<title>WeatheredOnward.net</title>
<link href="https://fonts.googleapis.com/css2?family=Questrial&family=Mulish:wght@700;800&display=swap" rel="stylesheet">
<style>
:root{
  --dark:#1b1b1b;
  --amber:#f7b500;
  --amber-deep:#e69a00;
  --orange-text:#d98a00;
  --page-bg:#e4e4e4;
  --panel:#ffffff;
  --ink:#1e1e1e;
  --field-border:#cfcfcf;
  --pill:#8c8c8c;
}
*{box-sizing:border-box;margin:0;padding:0}
html,body{width:1063px;height:1200px;overflow:hidden}
body{
  position:relative;font-family:"Questrial",sans-serif;color:var(--ink);
  background:var(--page-bg);
  background-image:radial-gradient(#d6d6d6 0.8px,transparent 0.9px);
  background-size:4px 4px;
}
.top-band{position:absolute;left:0;top:0;width:1063px;height:441px;
  background:linear-gradient(#222 0%,#151515 100%);border-top:3px solid var(--amber)}
.account-tab{position:absolute;left:857px;top:0;width:109px;height:23px;background:var(--amber);
  border-radius:0 0 3px 3px;font-family:"Mulish",sans-serif;font-weight:700;font-size:10px;
  display:flex;align-items:center;justify-content:center;gap:12px;color:#222}
.account-tab a{color:#222;text-decoration:underline}
.brand{position:absolute;left:126px;top:33px;width:161px;height:73px;background:#fff;border-radius:4px;
  display:flex;align-items:center;gap:6px;padding-left:10px}
.brand-mark{width:12px;height:12px;background:var(--amber-deep);flex:none}
.brand-name{font-family:"Mulish",sans-serif;font-weight:800;font-size:12.5px;color:var(--amber-deep);white-space:nowrap}
.nav{position:absolute;left:126px;top:136px;width:840px;height:27px;background:var(--amber);
  border-radius:3px 3px 0 0;display:flex;align-items:center}
.nav a{font-size:14px;color:#2b2b2b;text-decoration:none;height:27px;display:flex;align-items:center}
.nav .home{background:#fff;width:81px;justify-content:center;font-family:"Mulish",sans-serif;font-weight:700;border-radius:3px 0 0 0}
.nav .item{margin-left:20px;margin-right:30px}
.search{position:absolute;right:5px;top:5px;display:flex}
.search span{width:130px;height:17px;background:#fff;font-size:10px;color:#aaa;padding:2px 5px}
.search b{width:22px;height:17px;background:#111;color:#fff;font-family:"Mulish",sans-serif;font-size:11px;text-align:center;line-height:17px}
.hero{position:absolute;left:126px;top:163px;width:840px;height:324px;background:var(--panel);
  box-shadow:0 6px 10px rgba(0,0,0,.12)}
.hero-photo{position:absolute;left:8px;top:6px;width:583px;height:313px;
  background:radial-gradient(ellipse at 55% 45%,#d9a58a 0%,#c88f74 25%,#efe4dc 55%,#fafafa 80%)}
.hero-caption{position:absolute;left:10px;bottom:6px}
.hero-caption h2{font-weight:400;font-size:21px;color:#222}
.hero-caption h2 strong{font-family:"Mulish",sans-serif;font-weight:800}
.hero-caption p{font-size:11.5px;color:#333}
.dots{position:absolute;right:8px;bottom:10px;display:flex;gap:4px}
.dots i{width:9px;height:9px;border-radius:50%;background:#fff;box-shadow:0 0 2px rgba(0,0,0,.35)}
.dots i.on{background:var(--amber);box-shadow:0 0 0 2px #fff,0 0 3px 2px rgba(0,0,0,.2)}
.ask{position:absolute;left:610px;top:14px;width:222px}
.ask h3{font-weight:400;font-size:19px;color:#333}
.ask p{font-size:11.5px;color:#555;margin-top:6px;line-height:1.25}
.field{border:1px solid var(--field-border);border-radius:3px;height:23px;font-size:11px;color:#999;
  padding:4px 6px;margin-top:4px;background:#fff}
.field.first{margin-top:16px}
.field.tall{height:92px}
.row{display:flex;gap:5px}
.row .field{flex:1}
.row .btn-browse{width:63px;flex:none}
.btn-dark{display:block;margin-top:5px;height:23px;background:linear-gradient(#333,#0e0e0e);color:#fff;border-radius:3px;
  font-family:"Mulish",sans-serif;font-weight:700;font-size:12px;text-align:center;line-height:23px}
.content{position:absolute;left:126px;top:517px;width:840px;height:641px;background:var(--panel)}
.section-title{position:absolute;font-weight:400;font-size:19px;color:#333}
.divider{position:absolute;height:10px;background:radial-gradient(ellipse at 50% 0%,rgba(0,0,0,.12),transparent 70%)}
.article{position:absolute;left:16px;width:372px}
.article h4{font-family:"Mulish",sans-serif;font-weight:700;font-size:13px}
.meta{font-family:"Mulish",sans-serif;font-weight:700;font-size:9px;color:var(--orange-text);line-height:1.3}
.shares{display:flex;gap:2px;margin:3px 0 4px}
.shares i{width:14px;height:14px;border-radius:2px}
.s1{background:#f08a24}.s2{background:#f3a41a}.s3{background:#3b5b98}.s4{background:#c9c9c9}.s5{background:#42a9e0}.s6{background:#e8459a}
.article p{font-size:10.5px;color:#555;line-height:1.28}
.more{display:inline-block;margin-top:3px;background:var(--pill);color:#fff;font-size:10px;border-radius:4px;padding:1px 8px;
  box-shadow:inset 0 -1px 0 rgba(0,0,0,.2)}
.quadrant{position:absolute;width:180px}
.quadrant h4{font-family:"Mulish",sans-serif;font-weight:700;font-size:15px;color:#222;margin-bottom:8px;line-height:1.25}
.q-item{font-size:10.5px;color:#777;line-height:1.25;margin-bottom:7px}
.q-item b{font-family:"Mulish",sans-serif;font-weight:700;color:#555;font-size:10.5px;display:block}
.chat{position:absolute;left:482px;top:510px;width:230px}
.chat h3{font-weight:400;font-size:19px;color:#333;line-height:1.15}
.chat p{font-size:11.5px;color:#555;margin-top:10px;line-height:1.25}
.chat .btn-dark{margin-top:7px;width:221px}
</style>
</head>
<body>
<div class="top-band"></div>
<div class="account-tab"><a>Login</a><span>|</span><a>Register</a></div>
<div class="brand"><span class="brand-mark"></span><span class="brand-name">WeatheredOnward</span></div>

<nav class="nav">
  <a class="home">Home</a><a class="item">Profile</a><a class="item">Followers</a><a class="item">My Uploads</a>
  <div class="search"><span>search</span><b>Go</b></div>
</nav>

<section class="hero">
  <div class="hero-photo" role="img" aria-label="Photo of a young hand gently holding an elderly hand">
    <div class="hero-caption"><h2>Learn from <strong>Experience</strong></h2><p>Experience is the best teacher overall</p></div>
    <div class="dots"><i class="on"></i><i></i><i></i><i></i><i></i></div>
  </div>
  <form class="ask">
    <h3>Ask your Question</h3>
    <p>and get answered by the experienced people around the world</p>
    <div class="field first">Name</div>
    <div class="field">email address</div>
    <div class="field tall">your question</div>
    <div class="field">Select Quadrant</div>
    <div class="row"><div class="field">Upload Video (optional)</div><div class="field btn-browse">Browse</div></div>
    <span class="btn-dark">Get Answer</span>
  </form>
</section>

<main class="content">
  <h2 class="section-title" style="left:14px;top:12px">Fresh Articles</h2>
  <h2 class="section-title" style="left:485px;top:12px">Browse by Quadrant</h2>
  <div class="divider" style="left:20px;top:42px;width:790px"></div>

  <article class="article" style="top:65px"><h4>Problem in life with Money</h4><div class="meta">July 13, 2012<br>132 response, 8996 views</div><div class="shares"><i class="s1"></i><i class="s2"></i><i class="s3"></i><i class="s4"></i><i class="s5"></i><i class="s6"></i></div><p>This is Draftly's version &nbsp;of Lorem Ipsum. Proin gravida nibh vel velit auctor aliquet. Aenean sollicitudin, lorem quis bibendum auctor, nisi elit consequat ipsum, nec sagittis sem nibh id elit. Duis sed ...</p><span class="more">more</span></article>
  <article class="article" style="top:208px"><h4>Problem in life with Money</h4><div class="meta">July 13, 2012<br>132 response, 8996 views</div><div class="shares"><i class="s1"></i><i class="s2"></i><i class="s3"></i><i class="s4"></i><i class="s5"></i><i class="s6"></i></div><p>This is Draftly's version &nbsp;of Lorem Ipsum. Proin gravida nibh vel velit auctor aliquet. Aenean sollicitudin, lorem quis bibendum auctor, nisi elit consequat ipsum, nec sagittis sem nibh id elit. Duis sed ...</p><span class="more">more</span></article>
  <article class="article" style="top:351px"><h4>Problem in life with Money</h4><div class="meta">July 13, 2012<br>132 response, 8996 views</div><div class="shares"><i class="s1"></i><i class="s2"></i><i class="s3"></i><i class="s4"></i><i class="s5"></i><i class="s6"></i></div><p>This is Draftly's version &nbsp;of Lorem Ipsum. Proin gravida nibh vel velit auctor aliquet. Aenean sollicitudin, lorem quis bibendum auctor, nisi elit consequat ipsum, nec sagittis sem nibh id elit. Duis sed ...</p><span class="more">more</span></article>
  <article class="article" style="top:494px"><h4>Problem in life with Money</h4><div class="meta">July 13, 2012<br>132 response, 8996 views</div><div class="shares"><i class="s1"></i><i class="s2"></i><i class="s3"></i><i class="s4"></i><i class="s5"></i><i class="s6"></i></div><p>This is Draftly's version &nbsp;of Lorem Ipsum. Proin gravida nibh vel velit auctor aliquet. Aenean sollicitudin, lorem quis bibendum auctor, nisi elit consequat ipsum, nec sagittis sem nibh id elit. Duis sed ...</p><span class="more">more</span></article>

  <div class="quadrant" style="left:483px;top:70px"><h4>Financial Problems</h4>
    <div class="q-item"><b>Problem in life with Money</b>July 13, 2012<br>132 response, 8996 views</div>
    <div class="q-item"><b>Problem in life with Money</b>July 13, 2012<br>132 response, 8996 views</div>
    <div class="q-item"><b>Problem in life with Money</b>July 13, 2012<br>132 response, 8996 views</div>
    <span class="more">more</span></div>
  <div class="quadrant" style="left:672px;top:70px"><h4>Legal Matters</h4>
    <div class="q-item"><b>Problem in life with Money</b>July 13, 2012<br>132 response, 8996 views</div>
    <div class="q-item"><b>Problem in life with Money</b>July 13, 2012<br>132 response, 8996 views</div>
    <div class="q-item"><b>Problem in life with Money</b>July 13, 2012<br>132 response, 8996 views</div>
    <span class="more">more</span></div>
  <div class="quadrant" style="left:483px;top:290px"><h4>Medical &amp; Physical</h4>
    <div class="q-item"><b>Problem in life with Money</b>July 13, 2012<br>132 response, 8996 views</div>
    <div class="q-item"><b>Problem in life with Money</b>July 13, 2012<br>132 response, 8996 views</div>
    <div class="q-item"><b>Problem in life with Money</b>July 13, 2012<br>132 response, 8996 views</div>
    <span class="more">more</span></div>
  <div class="quadrant" style="left:672px;top:290px"><h4>Psychological &amp;<br>Spiritual</h4>
    <div class="q-item"><b>Problem in life with Money</b>July 13, 2012<br>132 response, 8996 views</div>
    <div class="q-item"><b>Problem in life with Money</b>July 13, 2012<br>132 response, 8996 views</div>
    <span class="more">more</span></div>

  <div class="divider" style="left:490px;top:497px;width:320px"></div>
  <section class="chat">
    <h3>Chat Online with a<br>Life Coach</h3>
    <p>and get answered by the experienced people around the world</p>
    <span class="btn-dark">Start Now</span>
  </section>
</main>
</body>
</html>
```